Coral Bay Pools New website

I currently operate a swimming pool service and repair business and looking for a re design for my website as it has been over 5 years since it was designed. current site is coralbaypoolslv.com

```html
<!DOCTYPE html>
<html lang="en">
<head>
<meta charset="utf-8">
<title>Coral Bay Pools</title>
<link rel="stylesheet" href="https://fonts.googleapis.com/css2?family=Poppins:ital,wght@0,400;0,500;0,600;1,400&family=Libre+Baskerville:wght@400;700&family=Great+Vibes&display=swap">
<style>
:root{
  --blue:#1d5c9c;
  --blue-dark:#164a80;
  --orange:#e8952a;
  --orange-light:#f7bd3a;
  --text:#222;
  --muted:#555;
  --white:#fff;
  --line:#d6d9de;
}
*{margin:0;padding:0;box-sizing:border-box}
html,body{width:1200px;height:3940px;overflow:hidden;background:var(--white)}
body{position:relative;font-family:'Poppins',sans-serif;color:var(--text)}
.abs{position:absolute}
.serif{font-family:'Libre Baskerville',serif}
.btn{position:absolute;display:flex;align-items:center;justify-content:center;background:linear-gradient(180deg,var(--orange-light),var(--orange));color:#1c1c1c;font-weight:600;font-size:14px;border-radius:12px;letter-spacing:.2px}
/* header */
.top-rule{left:25px;top:0;width:875px;height:2px;background:var(--blue)}
.brand{left:69px;top:56px;display:flex;align-items:center;gap:12px}
.brand-dot{width:34px;height:34px;border-radius:50%;background:var(--orange)}
.brand-name{font-family:'Libre Baskerville',serif;font-weight:700;font-size:26px;color:var(--blue)}
.phone{left:720px;top:44px;display:flex;align-items:center;gap:14px;font-size:24px;font-weight:500;color:#1c1c1c}
.phone-ico{width:48px;height:46px;border-radius:12px;background:linear-gradient(180deg,var(--orange-light),var(--orange));display:flex;align-items:center;justify-content:center}
.nav{left:461px;top:118px;display:flex;gap:38px;font-size:14px;color:#333}
.nav .on{color:var(--blue);font-weight:600}
/* hero */
.hero{left:0;top:188px;width:1200px;height:700px}
.hero-txt{left:0;width:1200px;text-align:center;color:var(--white)}
.welcome{top:327px;font-size:16px;font-weight:600}
.title{top:350px;font-family:'Libre Baskerville',serif;font-size:88px;letter-spacing:2px}
.script{top:380px;font-family:'Great Vibes',cursive;font-size:170px;color:var(--orange);left:40px}
.lead{top:596px;font-size:19px;line-height:30px}
/* features */
.feat{top:1020px;width:240px;text-align:center}
.feat-label{margin-top:18px;font-family:'Libre Baskerville',serif;font-weight:700;font-size:20px;line-height:25px;color:#222}
/* headings */
.h2{font-family:'Libre Baskerville',serif;font-weight:700;font-size:44px;color:var(--blue)}
.h2 span{color:var(--orange)}
.rule{height:3px;background:var(--orange);width:68px}
.rule::after{content:"";position:absolute;left:50%;top:-3px;width:9px;height:9px;border-radius:50%;background:var(--orange);transform:translateX(-50%)}
.rule{position:absolute}
/* about */
.about-sub{left:107px;top:1460px;width:490px;font-weight:600;font-size:20px;line-height:31px;color:#111}
.about-p{left:107px;top:1532px;width:488px;font-size:14.5px;line-height:27.5px;color:var(--muted);text-align:justify}
/* services */
.svc{top:2080px;width:516px;height:354px;background:var(--white);box-shadow:0 4px 14px rgba(0,0,0,.18)}
.svc-title{height:68px;display:flex;align-items:center;justify-content:center;font-family:'Libre Baskerville',serif;font-weight:700;font-size:26px;color:var(--blue)}
.svc-media{position:relative;height:286px}
.svc-media::before{content:"";position:absolute;left:50%;top:-1px;transform:translateX(-50%);border-left:16px solid transparent;border-right:16px solid transparent;border-top:16px solid var(--white);z-index:2}
.svc-copy{position:absolute;left:55px;right:55px;top:88px;color:var(--white);font-size:14.5px;line-height:22px;text-align:center}
/* testimonials */
.quote-card{top:2760px;width:464px;height:222px}
.quote-text{position:absolute;left:37px;top:90px;width:395px;font-style:italic;font-size:12.5px;line-height:21px;color:#444}
.person{top:3006px;display:flex;align-items:center;gap:16px}
.avatar{width:68px;height:68px;border-radius:50%;background:linear-gradient(160deg,#c9b7a5,#6e5a4b)}
.pname{font-weight:600;font-size:13.5px;color:#111}
.prole{font-size:11.5px;color:#333}
.dots{left:563px;top:3125px;display:flex;gap:5px}
.dots i{width:9px;height:9px;border-radius:50%;border:1px solid #555}
.dots i.on{background:#555}
/* footer */
.footer{left:0;top:3241px;width:1200px;height:699px}
.f-h{top:3560px;font-size:24px;font-weight:600;color:var(--white)}
.f-rule{top:3600px;height:2px;width:56px;background:var(--white)}
.f-links{left:482px;top:3628px;list-style:none;color:var(--white);font-size:14px}
.f-links li{height:32.5px;display:flex;align-items:center;gap:14px}
.f-links li::before{content:"";width:6px;height:6px;border-radius:50%;background:var(--white)}
.f-contact{left:797px;color:var(--white);font-size:14.5px;line-height:22px;display:flex;align-items:center;gap:18px}
.f-ico{width:38px;height:38px;border-radius:50%;background:var(--white);display:flex;align-items:center;justify-content:center;flex:none}
.social{top:3721px;width:36px;height:36px;border-radius:50%;background:var(--white)}
.f-line{left:75px;top:3822px;width:1050px;height:1px;background:rgba(255,255,255,.35)}
.copy{left:0;top:3856px;width:1200px;text-align:center;color:var(--white);font-size:15px}
</style>
</head>
<body>

<!-- header -->
<div class="abs top-rule"></div>
<div class="abs brand"><div class="brand-dot"></div><div class="brand-name">Coral Bay Pools</div></div>
<div class="abs phone">
  <div class="phone-ico"><svg width="22" height="22" viewBox="0 0 24 24"><path d="M6.6 10.8a15 15 0 0 0 6.6 6.6l2.2-2.2a1 1 0 0 1 1-.25 11 11 0 0 0 3.6.6 1 1 0 0 1 1 1V20a1 1 0 0 1-1 1A17 17 0 0 1 3 4a1 1 0 0 1 1-1h3.5a1 1 0 0 1 1 1 11 11 0 0 0 .6 3.6 1 1 0 0 1-.25 1z" fill="#1c1c1c"/></svg></div>
  (702) 555-0148
</div>
<div class="btn" style="left:965px;top:44px;width:168px;height:46px">CONTACT US</div>
<nav class="abs nav"><span class="on">HOME</span><span>ABOUT US</span><span>OUR SERVICES</span><span>FREE ESTIMATE</span><span>OUR TESTIMONIALS</span><span>OUR BLOG</span></nav>

<!-- hero -->
<svg class="abs hero" viewBox="0 0 1200 700" role="img" aria-label="Resort pool at dusk with palm trees, tinted blue">
  <defs><linearGradient id="hg" x1="0" y1="0" x2="0" y2="1"><stop offset="0" stop-color="#3a6d9f"/><stop offset=".6" stop-color="#1f5c98"/><stop offset="1" stop-color="#195694"/></linearGradient></defs>
  <path d="M0 0H1200V388C1010 470 820 696 600 696C380 696 190 470 0 362Z" fill="url(#hg)"/>
</svg>
<div class="abs hero-txt welcome">WELCOME TO</div>
<div class="abs hero-txt title">CORAL BAY</div>
<div class="abs hero-txt script">Pools</div>
<div class="abs hero-txt lead">The swimming pool at your facility should be properly maintained to<br>ensure your guests or residents are safe.</div>
<div class="btn" style="left:516px;top:686px;width:168px;height:46px">CONTACT US</div>

<!-- features -->
<div class="abs feat" style="left:65px">
  <svg width="240" height="148" viewBox="0 0 240 148"><path d="M120 14L226 74L120 134L14 74Z" fill="var(--orange)" stroke="var(--orange)" stroke-width="26" stroke-linejoin="round"/><path d="M120 28L200 74L120 120L40 74Z" fill="none" stroke="#fff" stroke-width="1.5" stroke-linejoin="round"/><g fill="none" stroke="#fff" stroke-width="2.5"><circle cx="122" cy="58" r="14"/><path d="M116 70l-4 14 10-5 10 5-4-14M92 96h14l18 6 24-12M92 90h12l16 6"/></g></svg>
  <div class="feat-label">Quality Well<br>Results</div>
</div>
<div class="abs feat" style="left:342px">
  <svg width="240" height="148" viewBox="0 0 240 148"><path d="M120 14L226 74L120 134L14 74Z" fill="var(--blue)" stroke="var(--blue)" stroke-width="26" stroke-linejoin="round"/><path d="M120 28L200 74L120 120L40 74Z" fill="none" stroke="#fff" stroke-width="1.5" stroke-linejoin="round"/><g fill="none" stroke="#fff" stroke-width="2.5"><circle cx="116" cy="56" r="12"/><path d="M94 106v-16a14 14 0 0 1 14-14h16a14 14 0 0 1 14 14M116 76v30"/><circle cx="140" cy="96" r="10"/><path d="M135 96l4 4 6-7"/></g></svg>
  <div class="feat-label">Professional &amp;<br>Trusted Staff</div>
</div>
<div class="abs feat" style="left:618px">
  <svg width="240" height="148" viewBox="0 0 240 148"><path d="M120 14L226 74L120 134L14 74Z" fill="var(--orange)" stroke="var(--orange)" stroke-width="26" stroke-linejoin="round"/><path d="M120 28L200 74L120 120L40 74Z" fill="none" stroke="#fff" stroke-width="1.5" stroke-linejoin="round"/><g fill="none" stroke="#fff" stroke-width="2.5"><circle cx="120" cy="74" r="22" stroke-dasharray="8 4"/><circle cx="120" cy="74" r="13"/><path d="M113 74l5 5 9-9"/></g></svg>
  <div class="feat-label">Committed To<br>Success</div>
</div>
<div class="abs feat" style="left:894px">
  <svg width="240" height="148" viewBox="0 0 240 148"><path d="M120 14L226 74L120 134L14 74Z" fill="var(--blue)" stroke="var(--blue)" stroke-width="26" stroke-linejoin="round"/><path d="M120 28L200 74L120 120L40 74Z" fill="none" stroke="#fff" stroke-width="1.5" stroke-linejoin="round"/><g fill="none" stroke="#fff" stroke-width="2.2"><path d="M100 50l3 6 6 1-4 4 1 6-6-3-6 3 1-6-4-4 6-1zM120 44l3 6 6 1-4 4 1 6-6-3-6 3 1-6-4-4 6-1zM140 50l3 6 6 1-4 4 1 6-6-3-6 3 1-6-4-4 6-1z"/><circle cx="104" cy="80" r="6"/><circle cx="136" cy="80" r="6"/><circle cx="120" cy="78" r="7"/><path d="M92 100a12 12 0 0 1 24 0M124 100a12 12 0 0 1 24 0M106 100a14 14 0 0 1 28 0"/></g></svg>
  <div class="feat-label">100% Clients<br>Satisfied</div>
</div>

<!-- about -->
<div class="abs h2" style="left:107px;top:1374px">About <span>Us</span></div>
<div class="rule" style="left:107px;top:1438px"></div>
<div class="abs about-sub">We are a full service pool company servicing the Las Vegas Valley.</div>
<p class="abs about-p">My name is Daniel and I'm the owner of Coral Bay pools. I recently started this business in 2016 to provide Las Vegas with excellent, reliable pool service. Just because we are a new company that doesn't mean we lack experience. I've been in the pool industry for seven years and counting and have managed everything from your backyard pool to olympic sized pools with five plus years managing casino properties as well.</p>
<div class="btn" style="left:107px;top:1740px;width:148px;height:56px;border-radius:18px">READ MORE</div>
<svg class="abs" style="left:662px;top:1370px" width="444" height="444" viewBox="0 0 444 444" role="img" aria-label="Backyard pool beside a lit modern house with tropical plants">
  <defs><linearGradient id="ag" x1="0" y1="0" x2="0" y2="1"><stop offset="0" stop-color="#4b5a3a"/><stop offset=".45" stop-color="#8a6a3e"/><stop offset=".6" stop-color="#27a6d2"/><stop offset="1" stop-color="#c9c2b6"/></linearGradient></defs>
  <path d="M222 18L426 222L222 426L18 222Z" fill="url(#ag)" stroke="url(#ag)" stroke-width="36" stroke-linejoin="round"/>
  <path d="M222 62L382 222L222 382L62 222Z" fill="none" stroke="#fff" stroke-width="2" stroke-linejoin="round"/>
</svg>

<!-- services -->
<div class="abs h2" style="left:0;width:1200px;text-align:center;top:1948px">Our <span>Services</span></div>
<div class="rule" style="left:566px;top:2012px"></div>
<div class="abs svc" style="left:77px">
  <div class="svc-title">Commercial Pool</div>
  <div class="svc-media" role="img" aria-label="Commercial pool deck, tinted blue" style="background:linear-gradient(180deg,#3f6f99,#215e98 60%,#1f5a94)">
    <p class="svc-copy">As a commercial property owner or manager, doing your job well requires you to be mindful of all the details. Every day is filled with a thousand different decisions, and when you need support for your facility, it's critical that the company you rely upon be prompt and responsive.</p>
  </div>
</div>
<div class="abs svc" style="left:607px">
  <div class="svc-title">Residential Pool</div>
  <div class="svc-media" role="img" aria-label="Family relaxing on a yellow float in a pool" style="background:linear-gradient(180deg,#5cc4ea,#8fd4ec 45%,#e9c35a 80%,#74c6e6)"></div>
</div>

<!-- testimonials -->
<div class="abs h2" style="left:0;width:1200px;text-align:center;top:2592px">Our <span>Testimonials</span></div>
<div class="rule" style="left:566px;top:2656px"></div>

<div class="abs quote-card" style="left:113px">
  <svg class="abs" width="464" height="260" viewBox="0 0 464 260" style="left:0;top:0"><path d="M92 1H444a19 19 0 0 1 19 19V202a19 19 0 0 1-19 19H120L92 248L84 221H20a19 19 0 0 1-19-19V20A19 19 0 0 1 20 1H36" fill="none" stroke="var(--line)" stroke-width="2"/></svg>
  <div class="abs serif" style="left:65px;top:-46px;font-size:110px;font-weight:700;color:var(--blue);line-height:1">&ldquo;</div>
  <div class="abs" style="left:346px;top:40px;font-size:15px;color:#f2b01e;letter-spacing:1px">★★★★<span style="color:#777">★</span></div>
  <p class="quote-text">Lorem ipsum dolor sit amet, consectetur adipiscing elit, sed do e iusmod tempor incididunt ut labore et dolore magna aliqua. Ut enim ad minim veniam, quis nostrud exercitation ullamco laboris nisi ut aliquip ex ea commodo consequat.</p>
</div>
<div class="abs person" style="left:221px"><div class="avatar" role="img" aria-label="Client portrait"></div><div><div class="pname">MARCUS HALE</div><div class="prole">Lorem ipsum</div></div></div>

<div class="abs quote-card" style="left:622px">
  <svg class="abs" width="464" height="260" viewBox="0 0 464 260" style="left:0;top:0"><path d="M92 1H444a19 19 0 0 1 19 19V202a19 19 0 0 1-19 19H120L92 248L84 221H20a19 19 0 0 1-19-19V20A19 19 0 0 1 20 1H36" fill="none" stroke="var(--line)" stroke-width="2"/></svg>
  <div class="abs serif" style="left:65px;top:-46px;font-size:110px;font-weight:700;color:var(--blue);line-height:1">&ldquo;</div>
  <div class="abs" style="left:346px;top:40px;font-size:15px;color:#f2b01e;letter-spacing:1px">★★★★<span style="color:#777">★</span></div>
  <p class="quote-text">Lorem ipsum dolor sit amet, consectetur adipiscing elit, sed do eiusmod tempor incididunt ut labore et dolore magna aliqua. Ut enim ad minim veniam, quis nostrud exercitation ullamco laboris nisi ut aliquip ex ea commodo consequat. Duis aute irure dolor in reprehenderit in voluptate velit.</p>
</div>
<div class="abs person" style="left:730px"><div class="avatar" role="img" aria-label="Client portrait"></div><div><div class="pname">PETER LOWELL</div><div class="prole">Lorem ipsum</div></div></div>

<div class="abs dots"><i class="on"></i><i></i><i></i><i></i></div>

<!-- footer -->
<svg class="abs footer" viewBox="0 0 1200 699" role="img" aria-label="Pool water background, tinted blue">
  <defs><linearGradient id="fg" x1="0" y1="0" x2="0" y2="1"><stop offset="0" stop-color="#1d5d9c"/><stop offset="1" stop-color="#1a5590"/></linearGradient></defs>
  <path d="M0 306C200 190 400 0 600 0C800 0 1000 190 1200 306V699H0Z" fill="url(#fg)"/>
</svg>
<div class="abs" style="left:76px;top:3600px;display:flex;align-items:center;gap:10px"><div style="width:26px;height:26px;border-radius:50%;background:var(--orange)"></div><div style="font-family:'Libre Baskerville',serif;font-weight:700;font-size:22px;color:var(--white)">Coral Bay Pools</div></div>
<div class="abs social" style="left:123px"></div>
<div class="abs social" style="left:172px"></div>
<div class="abs social" style="left:218px"></div>

<div class="abs f-h" style="left:479px">LINKS</div>
<div class="abs f-rule" style="left:479px"></div>
<ul class="abs f-links"><li>About Us</li><li>Our Services</li><li>Our Testimonials</li><li>Our Blog</li><li>Contact US</li></ul>

<div class="abs f-h" style="left:795px">CONTACT</div>
<div class="abs f-rule" style="left:795px"></div>
<div class="abs f-contact" style="top:3625px">
  <div class="f-ico"><svg width="16" height="18" viewBox="0 0 24 24"><path d="M12 2a7 7 0 0 0-7 7c0 5 7 13 7 13s7-8 7-13a7 7 0 0 0-7-7zm0 9.5A2.5 2.5 0 1 1 12 6.5a2.5 2.5 0 0 1 0 5z" fill="var(--blue)"/></svg></div>
  <div>Lorem ipsum,Lorem ipsum.<br>Lorem ipsum</div>
</div>
<div class="abs f-contact" style="top:3688px">
  <div class="f-ico"><svg width="16" height="16" viewBox="0 0 24 24"><path d="M6.6 10.8a15 15 0 0 0 6.6 6.6l2.2-2.2a1 1 0 0 1 1-.25 11 11 0 0 0 3.6.6 1 1 0 0 1 1 1V20a1 1 0 0 1-1 1A17 17 0 0 1 3 4a1 1 0 0 1 1-1h3.5a1 1 0 0 1 1 1 11 11 0 0 0 .6 3.6 1 1 0 0 1-.25 1z" fill="var(--blue)"/></svg></div>
  <div>(702) 555-0148</div>
</div>
<div class="abs f-contact" style="top:3743px">
  <div class="f-ico"><svg width="16" height="14" viewBox="0 0 24 20"><path d="M2 2h20v16H2z" fill="var(--blue)"/><path d="M2 2l10 8 10-8" fill="none" stroke="#fff" stroke-width="2"/></svg></div>
  <div>poolsolutions@coralbaypoolslv.com</div>
</div>

<div class="abs f-line"></div>
<div class="abs copy">©2018 Coral Bay Pools - Do not copy. All rights reserved.</div>

</body>
</html>
```